Business Card design, meridale shipping

I started a container shipping company which specialized in export of cars, motorcycles, boats and general cargo overseas. I need a business card that stands out of the pack and gives clients an idea of what I do. I have attached a sample that someone designed for me but I don't think its the right fit. However the info on it is accurate so can be used right on new card.

Reason: I would like my new logo which is being designed on KORVANTILE.COM as well to be implemented into my business card.

Shipping

```html
<!DOCTYPE html>
<html lang="en">
<head>
<meta charset="utf-8">
<title>Meridale Shipping – Business Card</title>
<link rel="stylesheet" href="https://fonts.googleapis.com/css2?family=Open+Sans:wght@400;600;700&display=swap">
<style>
  :root {
    --backdrop: #2b2f35;
    --brand-blue: #0a30f0;
    --accent-blue: #3d7fe0;
    --card-white: #f7f7f7;
    --ink: #2f2f2f;
    --rule: #d9d9d9;
    --paper-text: #ffffff;
  }
  * { box-sizing: border-box; margin: 0; padding: 0; }
  html, body {
    width: 1200px; height: 864px; overflow: hidden;
    background: var(--backdrop);
    font-family: "Open Sans", Arial, sans-serif;
  }
  .canvas { position: relative; width: 1200px; height: 864px; }
  .card {
    position: absolute; width: 620px; height: 354px;
    border-radius: 3px;
  }
  .card--front {
    left: 290px; top: 50px;
    background: var(--brand-blue);
    color: var(--paper-text);
  }
  .brand-name {
    position: absolute; left: 120px; top: 150px;
    font-weight: 600; font-size: 42px; line-height: 1;
  }
  .card--back {
    left: 290px; top: 450px;
    background: var(--card-white);
    color: var(--ink);
  }
  .holder { position: absolute; left: 44px; top: 104px; }
  .holder-name { font-weight: 600; font-size: 26px; line-height: 1.1; }
  .holder-role { font-size: 17px; color: var(--accent-blue); line-height: 1.2; }
  .back-brand {
    position: absolute; right: 40px; top: 62px;
    font-weight: 600; font-size: 24px; color: var(--brand-blue);
  }
  .divider {
    position: absolute; left: 44px; right: 40px; top: 176px;
    height: 1px; background: var(--rule);
  }
  .contact-list {
    position: absolute; right: 40px; top: 198px;
    list-style: none; text-align: right;
  }
  .contact-item {
    display: flex; justify-content: flex-end; align-items: center; gap: 10px;
    font-size: 17px; line-height: 26px; color: var(--ink);
  }
  .contact-icon { width: 18px; height: 18px; flex: none; }
</style>
</head>
<body>
<main class="canvas">
  <section class="card card--front" aria-label="Card front">
    <span class="brand-name">Meridale Shipping</span>
  </section>

  <section class="card card--back" aria-label="Card back">
    <div class="back-brand">Meridale Shipping</div>
    <div class="holder">
      <p class="holder-name">Daniel Harwood</p>
      <p class="holder-role">Managing Director</p>
    </div>
    <div class="divider"></div>
    <ul class="contact-list">
      <li class="contact-item">044-318-2075
        <svg class="contact-icon" viewBox="0 0 18 18" aria-hidden="true"><rect width="18" height="18" rx="2" fill="var(--brand-blue)"/><path d="M4 8c0-2 2-3 5-3s5 1 5 3l-2 .5-.5-1.5h-5L6 8.5z M5 12h8v2H5z" fill="#fff"/></svg>
      </li>
      <li class="contact-item">123-604-5512
        <svg class="contact-icon" viewBox="0 0 18 18" aria-hidden="true"><rect width="18" height="18" rx="2" fill="var(--brand-blue)"/><rect x="4" y="6" width="10" height="8" fill="#fff"/><rect x="6" y="3.5" width="6" height="3" fill="#fff"/></svg>
      </li>
      <li class="contact-item">123-604-5512
        <svg class="contact-icon" viewBox="0 0 18 18" aria-hidden="true"><rect width="18" height="18" rx="2" fill="var(--brand-blue)"/><rect x="6" y="3" width="6" height="12" rx="1" fill="#fff"/><rect x="7" y="5" width="4" height="7" fill="var(--brand-blue)"/></svg>
      </li>
      <li class="contact-item">info@meridaleship.com
        <svg class="contact-icon" viewBox="0 0 18 18" aria-hidden="true"><rect width="18" height="18" rx="2" fill="var(--brand-blue)"/><rect x="3.5" y="5" width="11" height="8" fill="#fff"/><path d="M3.5 5l5.5 4.5L14.5 5" fill="none" stroke="var(--brand-blue)" stroke-width="1"/></svg>
      </li>
      <li class="contact-item">www.meridaleship.com
        <svg class="contact-icon" viewBox="0 0 18 18" aria-hidden="true"><rect width="18" height="18" rx="2" fill="var(--brand-blue)"/><path d="M7.5 10.5l3-3 M6 9l-1.5 1.5a2 2 0 0 0 3 3L9 12 M12 9l1.5-1.5a2 2 0 0 0-3-3L9 6" fill="none" stroke="#fff" stroke-width="1.6" stroke-linecap="round"/></svg>
      </li>
    </ul>
  </section>
</main>
</body>
</html>
```